Lumvra App | Pre-Launch Homepage

Dear designer,
Lumvra is a soon to be launched innovative & free social platform for collaborative addictions quitting.
We require a design for our pre-launch homepage that will elevate our basic wireframes to the next level.
We would like the wireframes to serve as a guideline only, and not as a final version of the design. If you have cool ideas - we would appreciate your creativity!
* This is a pre-launch website for a mobile app, and as such the design must be consistent with the general style, design and atmosphere of the app (see screenshot in the shared Drive link).
* We liked the style and feel of the following website: http://tandelhub.example/ - Please let's use it as a reference as well.
* The existing text in the wireframes is there just to represent a place for text. Copy will be edited by us after the design is done.
Please find the wireframes attached, and all relevant design assets and app screenshots in the following Drive shared link -
https://files.example-share.net/open?id=7KQ204RtP3mNxa8Y2Lb61H9cdVzQ
Thanks,
Reginald
Industry/Entity Type
Social
Number of Pages Required
1 page
Look and feel
Each slider illustrates characteristics of the customer's brand and the style your logo design should communicate.

```html
<!DOCTYPE html>
<html lang="en">
<head>
<meta charset="utf-8">
<title>Lumvra App | Pre-Launch Homepage</title>
<link rel="stylesheet" href="https://fonts.googleapis.com/css2?family=Roboto:wght@300;400;500;700&display=swap">
<style>
:root{
  --orange:#f39a1e;
  --orange-dark:#e0851a;
  --ink:#2b2b30;
  --muted:#8a8a90;
  --light:#eef0f3;
  --white:#ffffff;
  --footer:#1d1d22;
  --device:#20243a;
}
*{box-sizing:border-box;margin:0;padding:0}
html,body{width:1200px;height:3284px;overflow:hidden}
body{font-family:"Roboto",Arial,sans-serif;color:var(--ink);background:var(--white);position:relative}
section,footer{position:absolute;left:0;width:1200px;overflow:hidden}
.abs{position:absolute}

/* hero */
.hero{top:0;height:620px;background:linear-gradient(180deg,#2c211d 0%,#4b3527 55%,#6a4a33 100%)}
.topbar{right:150px;top:22px;display:flex;gap:18px;align-items:center;font-size:12px;color:var(--white)}
.topbar span{padding-right:18px;border-right:1px solid rgba(255,255,255,.3)}
.brand{left:0;width:1200px;text-align:center;top:48px;font-size:44px;font-weight:700;color:var(--orange)}
.tagline{left:0;width:1200px;text-align:center;top:108px;font-size:13px;color:var(--orange)}
.hero-copy{left:120px;top:218px;width:340px;color:var(--white)}
.hero-copy h1{font-size:21px;font-weight:700;line-height:1.4}
.hero-copy p{font-size:13px;margin-top:24px;color:#e9dfd6}
.subscribe{display:flex;margin-top:14px}
.subscribe .field{width:210px;height:34px;background:var(--white);border-radius:3px 0 0 3px;font-size:11px;color:#aaa;padding:10px 12px}
.subscribe .btn{width:120px;height:34px;background:var(--orange);color:var(--white);font-size:12px;font-weight:500;display:flex;align-items:center;justify-content:center;border-radius:0 3px 3px 0}
.hero-devices{left:560px;top:190px;width:540px;height:380px;border-radius:14px;background:linear-gradient(135deg,rgba(255,255,255,.18),rgba(255,255,255,.06))}

/* features */
.features{top:620px;height:400px;background:var(--white)}
.feature{top:96px;width:240px;text-align:center}
.feature svg,.feature .icon-ph{display:block;margin:0 auto;width:70px;height:70px}
.feature h3{font-size:25px;font-weight:400;margin-top:42px;color:var(--ink)}
.feature p{font-size:12px;color:var(--muted);margin:14px auto 0;width:150px;line-height:1.5}
.icon-ph{border-radius:50%;background:#c9c9cc}

/* fun */
.fun{top:1020px;height:460px;background:linear-gradient(100deg,#4a4f5c 0%,#2a2d36 45%,#1e2028 100%)}
.phone{border-radius:22px;background:var(--device);padding:48px 10px}
.phone .screen{width:100%;height:100%;background:var(--orange)}
.section-title{font-size:28px;font-weight:400}
.copy p{font-size:12px;line-height:1.6;margin-top:14px}
.fun .copy{left:480px;top:110px;width:400px;color:#d7d9de}
.fun .section-title{color:var(--white)}

/* inspire */
.inspire{top:1480px;height:440px;background:var(--light)}
.inspire .copy{left:240px;top:92px;width:400px;color:var(--muted)}

/* achieve */
.achieve{top:1920px;height:480px;background:var(--white)}
.achieve h2{left:0;width:1200px;text-align:center;top:24px;font-size:30px;font-weight:400}
.achieve .lead{left:330px;width:540px;top:72px;text-align:center;font-size:12px;color:var(--muted);line-height:1.6}
.item{width:260px}
.item h4{font-size:11px;font-weight:700;letter-spacing:.5px}
.item p{font-size:10px;color:var(--muted);line-height:1.5;margin-top:6px}
.dot{width:30px;height:30px;display:flex;align-items:center;justify-content:center}

/* coming soon */
.coming{top:2400px;height:440px;background:linear-gradient(90deg,#efe2db 0%,#f6efea 55%,#f3f0ee 100%)}
.coming-phones{left:40px;top:30px;width:400px;height:380px;border-radius:16px;background:linear-gradient(160deg,#cfc9cf,#e7dcd6 60%,#f0e6df)}
.coming h2{left:620px;top:150px;font-size:30px;font-weight:400}
.stores{left:622px;top:204px;display:flex;gap:16px}
.stores span{width:30px;height:30px;border-radius:6px;background:#7d7f86}
.coming .note{left:622px;top:262px;font-size:12px;color:var(--muted)}
.coming .subscribe{position:absolute;left:622px;top:282px}
.coming .field{border:1px solid #ddd}

/* footer */
.footer{top:2840px;height:444px;background:var(--footer);color:#b9b9c0;text-align:center}
.footer .brand{top:36px;font-size:36px}
.footer .join{position:absolute;left:0;width:1200px;top:94px;font-size:13px;color:var(--white)}
.social{left:0;width:1200px;top:126px;display:flex;justify-content:center;gap:18px}
.social span{width:14px;height:14px;border-radius:50%;background:#d0d0d6}
.rule{left:0;top:188px;width:1200px;height:1px;background:#2e2e35}
.legal{left:0;width:1200px;top:232px;font-size:11px;line-height:1.8}
.legal strong{color:var(--white);font-weight:500}
.legal a{color:var(--orange);text-decoration:none}
.to-top{right:40px;top:120px;font-size:10px;color:#b9b9c0;text-align:center}
</style>
</head>
<body>

<section class="hero">
  <div class="abs topbar"><span>Contact Us</span>
    <svg width="14" height="14" viewBox="0 0 24 24"><path fill="#fff" d="M6.6 10.8a15 15 0 006.6 6.6l2.2-2.2a1 1 0 011-.25 11.4 11.4 0 003.6.6 1 1 0 011 1V20a1 1 0 01-1 1A17 17 0 013 4a1 1 0 011-1h3.5a1 1 0 011 1 11.4 11.4 0 00.6 3.6 1 1 0 01-.25 1z"/></svg>
  </div>
  <div class="abs brand">Lumvra</div>
  <div class="abs tagline">Welcome a Better Version of Yourself</div>
  <div class="abs hero-copy">
    <h1>Lumvra is a revolutionary &amp; free social platform for collaborative addictions quitting.</h1>
    <p>Subscribe below for the latest release and updates</p>
    <div class="subscribe"><div class="field">Enter your email here</div><div class="btn">Let Me Know</div></div>
  </div>
  <div class="abs hero-devices" role="img" aria-label="Lumvra app shown on laptop, tablet and phone screens"></div>
</section>

<section class="features">
  <div class="abs feature" style="left:180px">
    <svg viewBox="0 0 70 70"><circle cx="35" cy="35" r="30" fill="#e14b3b"/><circle cx="35" cy="35" r="14" fill="#fff"/><g fill="#fff"><rect x="31" y="5" width="8" height="14"/><rect x="31" y="51" width="8" height="14"/><rect x="5" y="31" width="14" height="8"/><rect x="51" y="31" width="14" height="8"/></g></svg>
    <h3>Never be alone</h3>
    <p>Forget what you know - Lumvra makes it fun to quit.</p>
  </div>
  <div class="abs feature" style="left:480px">
    <svg viewBox="0 0 70 70"><polygon points="35,4 44,26 67,27 49,42 55,65 35,52 15,65 21,42 3,27 26,26" fill="#e8b22a"/></svg>
    <h3>Network Power</h3>
    <p>Forget what you know - Lumvra makes it fun to quit.</p>
  </div>
  <div class="abs feature" style="left:780px">
    <div class="icon-ph" role="img" aria-label="Brain illustration"></div>
    <h3>Stay Motivated</h3>
    <p>Forget what you know - Lumvra makes it fun to quit.</p>
  </div>
</section>

<section class="fun" role="img" aria-label="Hand holding a phone running the Lumvra app">
  <div class="abs phone" style="left:260px;top:40px;width:170px;height:360px"><div class="screen"></div></div>
  <div class="abs copy">
    <h2 class="section-title">Fun</h2>
    <p>Forget what you know – Lumvra makes it fun to quit. The bond between you and your friends comes to life in our gamified approach to changing your habits.</p>
    <p>Lumvra gives you the opportunity to take an active role in helping your friends or people near you overcome addictions as a team. That's right, we turned the recovery process into a social game.</p>
  </div>
</section>

<section class="inspire">
  <div class="abs copy">
    <h2 class="section-title">Inspire</h2>
    <p>One of the most important factors for successful quitting is the ability to stay inspired during the process.</p>
    <p>That's why we designed Lumvra as a platform where you can inspire and be inspired by a supportive network of awesome Lumvra users.</p>
  </div>
  <div class="abs phone" style="left:740px;top:30px;width:170px;height:370px"><div class="screen"></div></div>
</section>

<section class="achieve">
  <h2 class="abs">Achieve</h2>
  <p class="abs lead">Lumvra is built on a pyramid of relationships that makes use of the Social Cognitive Theory to provide a powerful network of positive reinforcement. The bigger you make it, the stronger you get.</p>

  <div class="abs item" style="left:150px;top:170px"><h4>IN HAC HABITASSE PLATEA</h4><p>Quisque a nibh ut dolor tempus pretium. Donec vel lorem sit amet risus ultrices.</p></div>
  <div class="abs item" style="left:150px;top:284px"><h4>SED SEMPER NIBH PORTTITOR</h4><p>Quisque a nibh ut dolor tempus pretium. Donec vel lorem sit amet risus ultrices.</p></div>
  <div class="abs item" style="left:150px;top:398px"><h4>EASY TO CUSTOMIZE</h4><p>Quisque a nibh ut dolor tempus pretium. Donec vel lorem sit amet risus ultrices.</p></div>

  <div class="abs dot" style="left:410px;top:166px"><svg width="16" height="16" viewBox="0 0 24 24"><polygon points="12,2 15,9 22,9.5 16.5,14 18.5,21 12,17 5.5,21 7.5,14 2,9.5 9,9" fill="none" stroke="#555" stroke-width="2"/></svg></div>
  <div class="abs dot" style="left:405px;top:276px;width:40px;height:40px"><svg width="40" height="40" viewBox="0 0 40 40"><rect x="8" y="8" width="24" height="24" transform="rotate(45 20 20)" fill="var(--orange)"/></svg></div>
  <div class="abs dot" style="left:410px;top:394px"><svg width="16" height="16" viewBox="0 0 24 24"><rect x="3" y="3" width="18" height="18" rx="2" fill="none" stroke="#555" stroke-width="2"/></svg></div>

  <div class="abs phone" style="left:500px;top:156px;width:200px;height:300px;padding:40px 10px"><div class="screen"></div></div>

  <div class="abs dot" style="left:760px;top:166px"><svg width="16" height="16" viewBox="0 0 24 24"><circle cx="12" cy="12" r="9" fill="none" stroke="#555" stroke-width="2"/></svg></div>
  <div class="abs dot" style="left:760px;top:282px"><svg width="16" height="16" viewBox="0 0 24 24"><path d="M6.6 10.8a15 15 0 006.6 6.6l2.2-2.2a1 1 0 011-.25 11.4 11.4 0 003.6.6 1 1 0 011 1V20a1 1 0 01-1 1A17 17 0 013 4a1 1 0 011-1h3.5a1 1 0 011 1 11.4 11.4 0 00.6 3.6 1 1 0 01-.25 1z" fill="#555"/></svg></div>
  <div class="abs dot" style="left:760px;top:394px"><svg width="16" height="16" viewBox="0 0 24 24"><path d="M4 12l5 5L20 6" fill="none" stroke="#555" stroke-width="2.4"/></svg></div>

  <div class="abs item" style="left:810px;top:170px"><h4>ETIAM ELEMENTUM</h4><p>Quisque a nibh ut dolor tempus pretium. Donec vel lorem sit amet risus ultrices.</p></div>
  <div class="abs item" style="left:810px;top:284px"><h4>24/7 LIVE SUPPORT</h4><p>Quisque a nibh ut dolor tempus pretium. Donec vel lorem sit amet risus ultrices.</p></div>
  <div class="abs item" style="left:810px;top:398px"><h4>PELLENTESQUE INTEGER</h4><p>Quisque a nibh ut dolor tempus pretium. Donec vel lorem sit amet risus ultrices.</p></div>
</section>

<section class="coming">
  <div class="abs coming-phones" role="img" aria-label="Stack of phone screens showing the Lumvra app"></div>
  <h2 class="abs">Coming Soon</h2>
  <div class="abs stores"><span></span><span></span><span></span></div>
  <p class="abs note">Subscribe below for the latest release and updates</p>
  <div class="subscribe"><div class="field">Enter your email here</div><div class="btn">Let Me Know</div></div>
</section>

<footer class="footer">
  <div class="abs brand">Lumvra</div>
  <div class="join">Join the revolution</div>
  <div class="abs social"><span></span><span></span><span></span></div>
  <div class="abs to-top">
    <svg width="18" height="22" viewBox="0 0 18 22"><path d="M9 2L2 10h5v10h4V10h5z" fill="var(--orange)"/></svg>
    <div>Back to Top</div>
  </div>
  <div class="abs rule"></div>
  <div class="abs legal"><strong>Copyright © 2015 Lumvra Ltd.</strong><br><a>Contact Us</a> | <a>T&amp;C</a> | <a>Privacy Policy</a></div>
</footer>

</body>
</html>
```